Brochure for a civil enineering company in A4 format

I need a brochure design for our company TIRO Engineering S.r.l.. We are an engineering consultant company. Our main clients are from the infrastructure industry (geotechnical and underground sectors mainly).
We are looking for a 2 pages (4 faces) fold out design with a glued pocket where we can put individual data sheets.
I need A4 format pages.

Target Market(s)

We are an engineering consultant company. Our main clients are from the infrastructure industry (geotechnical and underground sectors mainly).

Industry/Entity Type

Civil Engineer

Font styles to use
Sans Serif

Requirements
Must have
• Overall: 2 pages in A4 format
Essential style. Bright and modern appearance.
Glued pocket
Logo integrated in a picture on the pocket where I would like to insert a slogan (… tiro engineering … reliable solutions …)
Attached are selected images which the designer can use and edit at their own discretion.
Some advice in the following (anyway designers are free to provide their solutions):
Outer sheets:
Front page with name, logo. It could be nice to have the “m” of the logo integrated in a pictures, also a modified picture (I mean modify one of the attached pictures) so to create a general image and do not tie the cover to a specific job.
Back page: offices address and contact email address. Nice to have one space for a slogan.
Inner sheet: text that I upload in the file “inside-sheets”, possibly with pictures on each sheet. In the right faces insert the glued pocket. On this pages insert the section OUR EXPERIENCE ….with a space for a picture of our team.
Nice to have
• Clean and essential design.
Pictures choosing from the atteched ones. Pictures could be modified in a very light manner to make them a general idea of the work ( I mean geotechnical world) without to be immediately linked to a specific site.
Should not have
• excessive frills

```html
<!DOCTYPE html>
<html lang="en">
<head>
<meta charset="utf-8">
<title>TIRO Engineering S.r.l. – Brochure Cover</title>
<link href="https://fonts.googleapis.com/css2?family=Montserrat:wght@300;400;600;800&display=swap" rel="stylesheet">
<style>
  :root {
    --ink: #111111;
    --blue: #1f5fc8;
    --blue-deep: #1746a0;
    --paper: #ffffff;
    --paper-shade: #eef0f2;
  }
  html, body {
    margin: 0;
    padding: 0;
    width: 900px;
    height: 1200px;
    overflow: hidden;
    background: var(--paper);
  }
  .cover {
    position: relative;
    width: 900px;
    height: 1200px;
    overflow: hidden;
    background: linear-gradient(180deg, var(--paper) 0%, var(--paper) 55%, var(--paper-shade) 100%);
    font-family: "Montserrat", sans-serif;
    color: var(--ink);
  }
  .cover-art {
    position: absolute;
    inset: 0;
    width: 900px;
    height: 1200px;
  }
  .brand {
    position: absolute;
    left: 70px;
    top: 110px;
  }
  .brand-name {
    margin: 0;
    font-size: 150px;
    font-weight: 600;
    line-height: 0.9;
    letter-spacing: -3px;
    color: var(--ink);
  }
  .brand-tagline {
    margin: 14px 0 0 6px;
    font-size: 15px;
    font-weight: 600;
    letter-spacing: 3.2px;
    text-transform: uppercase;
    color: var(--ink);
  }
  .slogan {
    position: absolute;
    right: 40px;
    top: 730px;
    margin: 0;
    text-align: right;
    line-height: 1;
  }
  .slogan-lead {
    display: block;
    font-size: 40px;
    font-weight: 300;
    margin-bottom: 14px;
  }
  .slogan-strong {
    display: block;
    font-size: 50px;
    font-weight: 800;
    letter-spacing: -1px;
    margin-bottom: 10px;
  }
  .slogan-soft {
    font-weight: 300;
  }
  .accent {
    color: var(--blue);
  }
  .web-address {
    position: absolute;
    right: 70px;
    top: 1068px;
    margin: 0;
    font-size: 22px;
    font-weight: 400;
    letter-spacing: 6px;
    color: var(--paper);
  }
</style>
</head>
<body>
<main class="cover">
  <svg class="cover-art" viewBox="0 0 900 1200" xmlns="http://www.w3.org/2000/svg">
    <defs>
      <linearGradient id="site-tones" x1="0" y1="0" x2="0.4" y2="1">
        <stop offset="0" stop-color="#f4f5f6"/>
        <stop offset="0.28" stop-color="#e6e9ea"/>
        <stop offset="0.42" stop-color="#7f9bb0"/>
        <stop offset="0.55" stop-color="#5f7a4a"/>
        <stop offset="0.72" stop-color="#8c8168"/>
        <stop offset="1" stop-color="#6d6556"/>
      </linearGradient>
      <radialGradient id="tunnel-tones" cx="0.55" cy="0.45" r="0.6">
        <stop offset="0" stop-color="#6b6a5c"/>
        <stop offset="0.6" stop-color="#3f3e38"/>
        <stop offset="1" stop-color="#23231f"/>
      </radialGradient>
    </defs>

    <path class="hero-photo" role="img" aria-label="Photograph of a hillside construction site above the sea, with terraced earthworks and orange safety fencing"
          d="M0 0 H900 V560 C700 620 420 700 0 720 Z" fill="url(#site-tones)"/>

    <path class="band band-blue" d="M0 720 C420 700 700 620 900 560 V600 C700 660 420 740 0 760 Z" fill="var(--blue)"/>
    <path class="band band-white" d="M0 760 C420 740 700 660 900 600 V616 C700 676 420 756 0 776 Z" fill="var(--paper)"/>
    <path class="band band-blue-thin" d="M0 776 C420 756 700 676 900 616 V640 C700 700 420 780 0 798 Z" fill="var(--blue-deep)"/>

    <circle cx="200" cy="800" r="140" fill="var(--paper)"/>
    <circle cx="200" cy="800" r="133" fill="none" stroke="var(--ink)" stroke-width="1.5"/>
    <circle cx="200" cy="800" r="128" fill="none" stroke="var(--ink)" stroke-width="4"/>
    <circle cx="200" cy="800" r="120" fill="none" stroke="var(--blue)" stroke-width="8"/>
    <circle class="inset-photo" role="img" aria-label="Photograph of an orange excavator working inside a tunnel under construction"
            cx="200" cy="800" r="112" fill="url(#tunnel-tones)"/>

    <path class="footer-band" d="M150 1040 H900 V1130 H110 Z" fill="var(--ink)"/>
    <path class="footer-stripe" d="M105 1138 H900 V1156 H98 Z" fill="var(--blue)"/>
  </svg>

  <header class="brand">
    <h1 class="brand-name">tiro</h1>
    <p class="brand-tagline">Tiro Engineering, Reliable Solutions</p>
  </header>

  <p class="slogan">
    <span class="slogan-lead">We <span class="accent">work</span> to</span>
    <span class="slogan-strong">mitigate risk <span class="slogan-soft accent">and</span></span>
    <span class="slogan-strong">reduce <span class="accent">uncertainty</span></span>
  </p>

  <p class="web-address">www.tiroengineering.org</p>
</main>
</body>
</html>
```